Web Design Project - Shipping Industry

Goals and Objectives
The objective of the new website is to create a more modern look and feel. The site will also allow for a more effective means of communicating with members while providing the public with information and developments in the local, regional and international shipping industry.
Scope
The website will highlight the history of the organisation inclusive of text and photographs. It will take visitors through the years from beginning to present. Information on the history of the shipping industry will also be included.
It will feature current articles on the organisation, its members and stakeholders in the shipping industry. Member information as well as pertinent details regarding the organisation’s subsidiaries will be documented for the website.
Information as it relates to shipping statistics, case studies, laws and regulations, international treaties and trade documents, shipping terms, careers in shipping, job opportunities, training opportunities, information for shippers including port listing and trade lanes will be main features of the content for the website.
The Association’s community involvement, industry calendar events and related links relevant industry members will also be featured.
Target Market
• The General Public;
• Members of the organization;
• Shipping Industry Stakeholders (local, regional and international);
• Tertiary students conducting research.
• Potential employees
• Potential Business Partners
Best Practice Bench Marketing
The following websites are being looked at:
• Korvel Quayworks - http://www.korvelquayworks.example/ (preferred look)
• Tessaly Maritime Association - http://www.tma-freight.example/ (like image transition on main page)
• Drovna - http://www.drovna.example (professional look)
• PLW - http://www.pelworth.example (preferred color: blue in logo)
• Quillo - http://www.quillo.example/electronics/tv-video-audio/ (preferred look for links page: image + short text below + visit site link)
Expected Result
• 3 - 5 pages which must include: [1] main page [2] standard page [3] links page

```html
<!DOCTYPE html>
<html lang="en">
<head>
<meta charset="utf-8">
<title>Meridane PCS — Home</title>
<link rel="stylesheet" href="https://fonts.googleapis.com/css2?family=Source+Sans+3:ital,wght@0,400;0,600;0,700;1,400&display=swap">
<style>
  :root {
    --backdrop: #dcebf8;
    --page: #ffffff;
    --navy: #14286a;
    --heading: #1b2f78;
    --text: #3a3a3a;
    --muted: #5a5a5a;
    --rule: #bdbdbd;
    --field-border: #8a8a8a;
    --dot: #e8eef4;
    --dot-active: #4f8fd6;
  }
  * { box-sizing: border-box; margin: 0; padding: 0; }
  html, body { width: 1200px; height: 800px; overflow: hidden; }
  body {
    background: var(--backdrop);
    font-family: "Source Sans 3", "Segoe UI", sans-serif;
    color: var(--text);
  }
  .page {
    position: absolute; left: 120px; top: 0;
    width: 960px; height: 800px;
    background: var(--page);
    box-shadow: 0 0 8px rgba(60, 90, 130, 0.25);
  }
  .brand {
    position: absolute; left: 10px; top: 24px;
    font-size: 23px; font-weight: 700; letter-spacing: 2.5px;
    color: var(--navy); text-transform: uppercase;
  }
  .utility {
    position: absolute; right: 10px; top: 8px;
    display: flex; align-items: center; font-size: 13px; color: var(--text);
  }
  .utility .item { display: flex; align-items: center; gap: 8px; padding: 0 18px; }
  .utility .item + .item { border-left: 1px solid #cfcfcf; }
  .utility .search { padding-right: 0; }
  .search-field {
    width: 162px; height: 24px; border: 1px solid var(--field-border);
    border-radius: 2px; position: relative;
  }
  .search-field svg { position: absolute; right: 4px; top: 3px; }
  .main-nav {
    position: absolute; right: 10px; top: 60px;
    display: flex; gap: 41px; font-size: 15px; letter-spacing: 0.4px; color: var(--muted);
  }
  .main-nav .current { color: var(--navy); font-weight: 600; }
  .hero {
    position: absolute; left: 10px; top: 88px; width: 940px; height: 367px;
    background: linear-gradient(100deg, #c9c1a4 0%, #9a8f78 22%, #7c7e86 45%, #b59e7c 62%, #8f8a86 80%, #c6b9a3 100%);
  }
  .hero-shadow {
    position: absolute; left: 50px; top: 455px; width: 860px; height: 28px;
    background: radial-gradient(ellipse at 50% 0%, rgba(0,0,0,0.35), rgba(0,0,0,0) 70%);
  }
  .slider-dots { position: absolute; right: 10px; bottom: 9px; display: flex; gap: 7px; }
  .slider-dots span {
    width: 13px; height: 13px; border-radius: 50%;
    background: var(--dot); border: 1px solid #a9b3bd;
  }
  .slider-dots .active { background: var(--dot-active); border-color: #8fb6e0; }
  .feature {
    position: absolute; top: 510px; width: 165px;
  }
  .feature h2, .terminal h2 {
    font-size: 13px; font-weight: 600; color: var(--heading); margin-bottom: 5px;
  }
  .thumb { width: 161px; height: 108px; border: 1px solid #777; }
  .thumb-grey { background: linear-gradient(100deg, #d8d8d8, #7d7d7d 45%, #bdbdbd 70%, #8a8a8a); }
  .thumb-warm { background: linear-gradient(100deg, #d9c6a2, #8c7a62 45%, #c8ae86 70%, #7f7468); }
  .thumb-violet { background: linear-gradient(100deg, #e3b8e6, #9a4fa0 45%, #d58fd8 70%, #8a5a90); }
  .feature p, .terminal p {
    font-size: 10.5px; line-height: 1.27; color: var(--text); margin-top: 6px;
  }
  .terminal { position: absolute; left: 550px; top: 510px; width: 400px; }
  .terminal-form { display: flex; gap: 14px; margin: 8px 0 0 60px; }
  .select-field {
    width: 162px; height: 23px; border: 1px solid var(--field-border);
    font-size: 10px; font-style: italic; padding: 4px 6px; position: relative;
  }
  .select-field .arrow {
    position: absolute; right: 2px; top: 2px; width: 16px; height: 17px;
    border: 1px solid #8a8a8a; background: linear-gradient(#f4f4f4, #d6d6d6);
  }
  .submit {
    width: 82px; height: 23px; border: 1px solid #8a8a8a; border-radius: 2px;
    background: linear-gradient(#f7f7f7, #d9d9d9);
    font-size: 12px; text-align: center; line-height: 21px; color: #222;
  }
  .terminal h2.about { margin-top: 24px; }
  .terminal p + p { margin-top: 12px; }
  .footer {
    position: absolute; left: 10px; top: 750px; width: 940px;
    border-top: 1px solid var(--rule);
    display: flex; justify-content: space-between; padding-top: 11px;
    font-size: 12px; color: var(--text);
  }
  .footer-links span + span::before { content: "|"; margin: 0 6px; }
  .follow { display: flex; align-items: center; gap: 8px; }
  .social { width: 15px; height: 15px; border-radius: 2px; background: #6f86a8; }
</style>
</head>
<body>
  <div class="page">
    <div class="brand">Meridane PCS</div>

    <div class="utility">
      <div class="item">
        <svg width="14" height="18" viewBox="0 0 14 18" aria-hidden="true">
          <path d="M7 1a6 6 0 0 0-6 6c0 4.5 6 10 6 10s6-5.5 6-10a6 6 0 0 0-6-6z" fill="#1b2f78"/>
          <circle cx="7" cy="7" r="2.3" fill="#fff"/>
        </svg>
        Locate a Terminal
      </div>
      <div class="item">Corporate</div>
      <div class="item search">Search
        <div class="search-field">
          <svg width="16" height="16" viewBox="0 0 16 16" aria-hidden="true">
            <circle cx="6" cy="6" r="4.5" fill="none" stroke="#555" stroke-width="1.6"/>
            <line x1="9.4" y1="9.4" x2="14.5" y2="14.5" stroke="#555" stroke-width="2"/>
          </svg>
        </div>
      </div>
    </div>

    <nav class="main-nav">
      <span class="current">Home</span>
      <span>About Us</span>
      <span>Sustainabiity</span>
      <span>News</span>
      <span>Careers</span>
      <span>Links</span>
      <span>Contact Us</span>
    </nav>

    <div class="hero-shadow"></div>
    <div class="hero" role="img" aria-label="Warehouse aisle with tall steel racks holding wrapped pallets of cartons">
      <div class="slider-dots"><span class="active"></span><span></span><span></span><span></span></div>
    </div>

    <section class="feature" style="left:10px">
      <h2>Careers</h2>
      <div class="thumb thumb-grey" role="img" aria-label="Black and white view of warehouse racking"></div>
      <p>Lorem ipsum dolor sit amet, consectetuer adipiscing elit. Nam cursus. Morbi ut mi. Nullam enim leo, egestas id, condimentum at, laoreet mattis, massa. Sed eleifend nonummy diam.</p>
    </section>

    <section class="feature" style="left:190px">
      <h2>lifting global trade</h2>
      <div class="thumb thumb-warm" role="img" aria-label="Warehouse racking with pallets of goods"></div>
      <p>Lorem ipsum dolor sit amet, consectetuer adipiscing elit. Nam cursus. Morbi ut mi. Nullam enim leo, egestas id, condimentum at, laoreet mattis, massa. Sed eleifend nonummy diam.</p>
    </section>

    <section class="feature" style="left:370px">
      <h2>Corporate video</h2>
      <div class="thumb thumb-violet" role="img" aria-label="Violet-tinted still of warehouse racking for the corporate video"></div>
      <p>Lorem ipsum dolor sit amet, consectetuer adipiscing elit. Nam cursus. Morbi ut mi. Nullam enim leo, egestas id, condimentum at, laoreet mattis, massa. Sed eleifend nonummy diam.</p>
    </section>

    <section class="terminal">
      <h2>Select a terminal</h2>
      <div class="terminal-form">
        <div class="select-field">Select a terminal
          <span class="arrow">
            <svg width="14" height="15" viewBox="0 0 14 15" aria-hidden="true"><path d="M3 5h8l-4 5z" fill="#333"/></svg>
          </span>
        </div>
        <div class="submit">Submit</div>
      </div>
      <h2 class="about">about korvel quayworks</h2>
      <p>Lorem ipsum dolor sit amet, consectetuer adipiscing elit. Nam cursus. Morbi ut mi. Nullam enim leo, egestas id, condimentum at, laoreet mattis, massa. Sed eleifend nonummy diam. Lorem ipsum dolor sit amet, consectetuer adipiscing elit. Nam cursus. Morbi ut mi. Nullam enim leo, egestas id, condimentum at, laoreet mattis, massa.</p>
      <p>Sed eleifend nonummy diam.Lorem ipsum dolor sit amet, consectetuer adipiscing elit. Nam cursus. Morbi ut mi. Nullam enim leo, egestas id, condimentum at, laoreet mattis, massa. Sed eleifend nonummy diam.</p>
    </section>

    <footer class="footer">
      <div class="footer-links"><span>Contact Information</span><span>Legal Notice</span><span>About This Site</span></div>
      <div class="follow">Follow us :
        <span class="social" aria-label="Social link one"></span>
        <span class="social" aria-label="Social link two"></span>
        <span class="social" aria-label="Social link three"></span>
      </div>
    </footer>
  </div>
</body>
</html>
```